Business card for Luxury Portable Restroom Trailer company

We are a Luxury Portable Restroom Trailer Company Called FALCRIDGE HIRES. Based in Orange County California. We provide portable restroom trailers for events, such as, Weddings, Concerts, Charity events, Sporting events, Tournaments, Corporate events, ect. We rent and Sell the Luxury restrooms. Our colors are white, grey, and Orange. As you will see in the logo we uploaded.
There are 2 people in the company so the names and titles will change for the 3 people but card will remain the same. Here is the information for each Person: Dwight Penner CFO 555 318-0476
next Person: Leon Marchetti VP 555 318-0476
Next Person: Owen Marchetti CEO 555 318-0476
Information to include on the card: Luxury Restroom Trailers Rental and Sales. Weddings, Concerts, Charity, Sporting and Corp. Events.

```html
<!DOCTYPE html>
<html lang="en">
<head>
<meta charset="utf-8">
<title>Falcridge Hires – Business Card</title>
<link rel="stylesheet" href="https://fonts.googleapis.com/css2?family=Roboto:wght@400;700&display=swap">
<style>
  :root {
    --orange: #e0611f;
    --grey: #5a5a5a;
    --dark: #2a2a2a;
    --ink: #333333;
    --white: #ffffff;
    --backdrop: #2d2e30;
  }
  html, body {
    margin: 0;
    padding: 0;
    width: 1200px;
    height: 912px;
    overflow: hidden;
    background: var(--backdrop);
    font-family: "Roboto", Arial, sans-serif;
  }
  .canvas {
    position: relative;
    width: 1200px;
    height: 912px;
  }
  .card {
    position: absolute;
    width: 560px;
    height: 320px;
    border-radius: 18px;
    box-sizing: border-box;
    overflow: hidden;
  }
  .card--front {
    left: 70px;
    top: 90px;
    background: var(--orange);
    color: var(--white);
  }
  .card--back {
    left: 570px;
    top: 500px;
    background: var(--white);
    color: var(--ink);
  }

  /* wordmark */
  .wordmark {
    display: flex;
    align-items: center;
    gap: 12px;
    font-weight: 700;
    letter-spacing: 1px;
    white-space: nowrap;
  }
  .wordmark__square {
    display: block;
    background: currentColor;
  }
  .card--front .wordmark {
    position: absolute;
    left: 0;
    right: 0;
    top: 92px;
    justify-content: center;
    font-size: 40px;
    color: var(--white);
  }
  .card--front .wordmark__square { width: 22px; height: 22px; background: var(--grey); }

  .tagline {
    position: absolute;
    left: 0;
    right: 0;
    top: 192px;
    margin: 0;
    text-align: center;
    font-size: 15px;
    line-height: 1.45;
    font-weight: 400;
  }

  .card--back .wordmark {
    position: absolute;
    right: 34px;
    top: 34px;
    font-size: 24px;
    color: var(--grey);
  }
  .card--back .wordmark__square { width: 14px; height: 14px; background: var(--orange); }

  .contact {
    position: absolute;
    right: 34px;
    top: 96px;
    margin: 0;
    padding: 0;
    list-style: none;
    font-size: 13px;
    line-height: 1.55;
    text-align: right;
  }
  .contact li {
    display: flex;
    justify-content: flex-end;
    align-items: center;
    gap: 7px;
  }
  .contact svg { width: 11px; height: 11px; fill: var(--orange); }
  .contact li:first-child { margin-bottom: 8px; }

  .rule {
    position: absolute;
    height: 1px;
    background: var(--ink);
  }
  .rule--contact { left: 150px; right: 34px; top: 126px; }
  .rule--person { left: 34px; width: 200px; top: 252px; }

  .person {
    position: absolute;
    left: 34px;
    top: 196px;
  }
  .person__name {
    margin: 0;
    font-size: 22px;
    font-weight: 700;
    color: var(--orange);
  }
  .person__title {
    margin: 2px 0 0;
    font-size: 14px;
    color: var(--grey);
  }
  .address {
    position: absolute;
    left: 34px;
    top: 260px;
    margin: 0;
    font-style: normal;
    font-size: 14px;
    line-height: 1.4;
    color: var(--ink);
  }
</style>
</head>
<body>
<main class="canvas">
  <section class="card card--front" aria-label="Card front">
    <div class="wordmark"><span class="wordmark__square"></span>FALCRIDGE HIRES</div>
    <p class="tagline">Luxury Restroom Trailers Rental and Sales<br>Weddings, Concerts, Charity, Sporting and Corp Events</p>
  </section>

  <section class="card card--back" aria-label="Card back">
    <div class="wordmark"><span class="wordmark__square"></span>FALCRIDGE HIRES</div>
    <ul class="contact">
      <li>555 318-0476
        <svg viewBox="0 0 24 24" aria-hidden="true"><path d="M6.6 10.8a15.1 15.1 0 0 0 6.6 6.6l2.2-2.2a1 1 0 0 1 1-.25 11.4 11.4 0 0 0 3.6.57 1 1 0 0 1 1 1V20a1 1 0 0 1-1 1A17 17 0 0 1 3 4a1 1 0 0 1 1-1h3.5a1 1 0 0 1 1 1c0 1.25.2 2.45.57 3.57a1 1 0 0 1-.25 1z"/></svg>
      </li>
      <li>name@FALCRIDGE.com
        <svg viewBox="0 0 24 24" aria-hidden="true"><path d="M2 5h20v14H2z M3 6l9 7 9-7" stroke="#fff" stroke-width="1.5"/></svg>
      </li>
      <li>www.FALCRIDGE.com
        <svg viewBox="0 0 24 24" aria-hidden="true"><circle cx="12" cy="12" r="11"/></svg>
      </li>
    </ul>
    <div class="rule rule--contact"></div>

    <div class="person">
      <p class="person__name">Dwight Penner</p>
      <p class="person__title">CFO</p>
    </div>
    <div class="rule rule--person"></div>
    <address class="address">2107 Harbor Crest Lane<br>Fountain Valley, CA 92708</address>
  </section>
</main>
</body>
</html>
```